The Quiet Lantern Business Card

I need a business card designed for The Quiet Lantern. The company provides on site support and education to end consumers in the ins and outs of all our digital devices. We advise on product purchase, installation, maintenance and troubleshooting. Anything from cordless phones to home networks.
My initial concept is double sided with the white logo on green on one side and contact details and a small logo on the flip side (logo package attached)
Contact Details:
Pablo Strand
Managing Director
PO Box 4
Marlow Heights, NSW 2091
Phone: 0438 559 106
email: pablo@quietlantern.com.au
web: www.quietlantern.com.au
Target Market(s)
Busy professionals and retired folks.
Industry/Entity Type
Education
Look and feel

```html
<!DOCTYPE html>
<html lang="en">
<head>
<meta charset="utf-8">
<title>The Quiet Lantern – Business Card</title>
<link rel="stylesheet" href="https://fonts.googleapis.com/css2?family=Raleway:wght@300;400;500&display=swap">
<style>
  :root {
    --navy: #0d2c45;
    --green: #7dbb2f;
    --paper: #f7f8f8;
    --ink: #2d3339;
    --fold: #b9bcbf;
    --backdrop: #2a2c2e;
  }
  * { box-sizing: border-box; margin: 0; padding: 0; }
  html, body { width: 1200px; height: 898px; overflow: hidden; }
  body {
    background: var(--backdrop);
    font-family: "Raleway", sans-serif;
    position: relative;
  }
  .card {
    position: absolute;
    left: 280px;
    width: 640px;
    height: 366px;
    background: var(--paper);
    overflow: hidden;
    box-shadow: 0 14px 30px rgba(0,0,0,.45);
  }
  .card--front { top: 58px; }
  .card--back { top: 474px; }

  /* front */
  .front-band {
    position: absolute; top: 0; bottom: 0; width: 140px;
    background: var(--navy);
  }
  .front-band--left { left: 0; }
  .front-band--right { right: 0; }
  .front-logo {
    position: absolute; left: 140px; right: 140px; top: 0; bottom: 0;
    display: flex; flex-direction: column; align-items: center; justify-content: center;
    gap: 18px;
  }
  .logo-dot { width: 38px; height: 38px; border-radius: 50%; background: var(--green); flex: none; }
  .logo-name {
    color: var(--navy); font-weight: 300; text-align: center; line-height: 1.05;
    letter-spacing: .04em;
  }
  .front-logo .logo-name { font-size: 40px; }

  /* back */
  .back-panel {
    position: absolute; top: 0; bottom: 0; right: 0; width: 240px;
    background: var(--navy);
  }
  .name-strip {
    position: absolute; left: 350px; right: 0; top: 132px; height: 32px;
    background: var(--green);
    clip-path: polygon(16px 0, 100% 0, 100% 100%, 0 100%);
    display: flex; align-items: center; padding-left: 26px; gap: 9px;
    color: #fff; font-size: 12px; font-weight: 400; letter-spacing: .06em; text-transform: uppercase;
    white-space: nowrap;
  }
  .name-strip .title { font-size: 9px; }
  .name-strip .divider { width: 1px; height: 16px; background: #fff; flex: none; }
  .strip-fold { position: absolute; left: 350px; top: 164px; }
  .back-logo {
    position: absolute; left: 46px; top: 70px;
    display: flex; align-items: center; gap: 14px;
  }
  .back-logo .logo-dot { width: 28px; height: 28px; }
  .back-logo .logo-name { font-size: 30px; text-align: left; white-space: nowrap; }
  .contact {
    position: absolute; left: 46px; top: 218px;
    color: var(--ink); font-size: 11.5px; line-height: 1.45; letter-spacing: .03em;
  }
  .contact address { font-style: normal; margin-bottom: 10px; }
  .contact ul { list-style: none; }
  .contact li { display: flex; align-items: center; gap: 8px; height: 18px; white-space: nowrap; }
  .contact svg { width: 11px; height: 11px; fill: var(--ink); flex: none; }
</style>
</head>
<body>

<section class="card card--front" aria-label="Card front">
  <div class="front-band front-band--left"></div>
  <div class="front-logo">
    <span class="logo-dot"></span>
    <p class="logo-name">The Quiet<br>Lantern</p>
  </div>
  <div class="front-band front-band--right"></div>
</section>

<section class="card card--back" aria-label="Card back">
  <div class="back-panel"></div>
  <div class="name-strip">
    <span class="name">Pablo Strand</span>
    <span class="divider"></span>
    <span class="title">Managing Director</span>
  </div>
  <svg class="strip-fold" width="60" height="28" viewBox="0 0 60 28" aria-hidden="true">
    <polygon points="0,0 60,0 60,28" fill="var(--fold)"/>
  </svg>

  <div class="back-logo">
    <span class="logo-dot"></span>
    <p class="logo-name">The Quiet Lantern</p>
  </div>

  <div class="contact">
    <address>PO Box 4<br>Marlow Heights, NSW 2091</address>
    <ul>
      <li><svg viewBox="0 0 12 12"><path d="M2.5 1 4.5 3 3.6 4.4c.8 1.6 2.2 3 3.9 3.9L8.9 7.4 11 9.4 9.8 11C5 10.7 1.3 7 1 2.2Z"/></svg>0438 559 106</li>
      <li><svg viewBox="0 0 12 12"><path d="M3 0h6v12H3Zm1 1.5v7.5h4V1.5Zm2 8.5a.7.7 0 1 0 0 1.4.7.7 0 0 0 0-1.4Z"/></svg>0438 559 106</li>
      <li><svg viewBox="0 0 12 12"><path d="M0 2h12v8H0Zm1 1 5 3.6L11 3v-.2H1Z"/></svg>pablo@quietlantern.com.au</li>
      <li><svg viewBox="0 0 12 12"><path d="M6 0a6 6 0 1 0 0 12A6 6 0 0 0 6 0Zm0 1.2c.9.8 1.5 2.5 1.6 4.2H4.4C4.5 3.7 5.1 2 6 1.2ZM1.2 6.6h2.2c.1 1.6.6 3 1.3 4A4.8 4.8 0 0 1 1.2 6.6Zm0-1.2a4.8 4.8 0 0 1 3.5-4c-.7 1-1.2 2.4-1.3 4Zm3.2 1.2h3.2C7.5 8.3 6.9 10 6 10.8c-.9-.8-1.5-2.5-1.6-4.2Zm4.2 0h2.2a4.8 4.8 0 0 1-3.5 4c.7-1 1.2-2.4 1.3-4Zm0-1.2c-.1-1.6-.6-3-1.300-4a4.8 4.8 0 0 1 3.5 4Z"/></svg>www.quietlantern.com.au</li>
    </ul>
  </div>
</section>

</body>
</html>
```